Business Card Design Project

We are not a new company, but renamed to "Vantorin Kitchens" last year. We specialize in modern high-end cabinetry imports. We would like to communicate a sense of quality and cutting edge technology. Ideally the design would incorporate our logo colors, silver, red and preferably a black, matte background. Though we are open to suggestions.
Logo is attached.
Edit: I have attached rough drafts of the previous cards, this way you will have all necessary content that needs to go on the cards.
Updates
Project Deadline Extended
Reason: We have received a lot of great designs, but due to the sheer number we couldn't respond to all. We will extend the deadline for another 7 days to finalize and provide feedback to designers.
Thank you for your hard work!
Industry/Entity Type
Business
Look and feel
Each slider illustrates characteristics of the customer's brand and the style your logo design should communicate.

```html
<!DOCTYPE html>
<html lang="en">
<head>
<meta charset="utf-8">
<title>Vantorin Kitchens – Business Cards</title>
<link rel="stylesheet" href="https://fonts.googleapis.com/css2?family=Michroma&family=Roboto+Condensed:wght@700&family=Arimo&display=swap">
<style>
  :root {
    --stage: #e4e1dc;
    --label: #2a2622;
    --card: #050505;
    --card-soft: #1c1c1e;
    --silver-light: #e6e6e6;
    --silver: #bdbdbd;
    --silver-dark: #6f6f6f;
    --red: #e3202a;
    --white: #f4f4f4;
    --dot-tone: #3a3a3c;
  }
  * { margin: 0; padding: 0; box-sizing: border-box; }
  html, body { width: 1200px; height: 788px; overflow: hidden; }
  body { background: var(--stage); position: relative; font-family: "Michroma", sans-serif; }

  .view-label {
    position: absolute; width: 300px; text-align: center;
    font-family: "Arimo", sans-serif; font-size: 20px; color: var(--label);
  }

  .card {
    position: absolute; width: 525px; height: 300px;
    border-radius: 22px; background: var(--card); overflow: hidden; color: var(--white);
  }

  .brand-mark {
    position: absolute; background: linear-gradient(180deg, var(--silver-light), var(--silver-dark));
  }
  .brand-name {
    position: absolute; white-space: nowrap; color: var(--silver);
    letter-spacing: 0.5px; text-transform: uppercase;
  }

  /* front */
  .front .brand-mark { left: 148px; top: 28px; width: 40px; height: 40px; }
  .front .brand-name { left: 20px; top: 88px; font-size: 21px; }

  .name-band {
    position: absolute; left: 278px; top: 140px; width: 247px; height: 50px;
    background: linear-gradient(90deg, #8a8a8a, #d8d8d8 55%, #b5b5b5);
  }
  .name-band::after {
    content: ""; position: absolute; right: 0; top: 0; width: 28px; height: 100%; background: var(--red);
  }
  .person-name {
    position: absolute; left: 12px; top: 8px; font-size: 14px; letter-spacing: 2px;
    color: var(--white); text-transform: uppercase;
  }
  .person-role {
    position: absolute; left: 12px; top: 31px; font-family: "Roboto Condensed", sans-serif;
    font-weight: 700; font-size: 11px; color: var(--white); text-transform: uppercase;
  }

  .contact-list { position: absolute; left: 290px; top: 208px; list-style: none; }
  .contact-list li {
    display: flex; align-items: center; gap: 8px; height: 19.5px;
    font-size: 10px; letter-spacing: 1px;
  }
  .contact-list svg { width: 11px; height: 11px; fill: var(--silver); }
  .address {
    position: absolute; left: 24px; top: 250px; font-size: 10px; line-height: 19px; letter-spacing: 1px;
  }

  /* back */
  .back-carbon {
    background: radial-gradient(ellipse at 50% 45%, var(--card-soft), #0a0a0b 75%);
  }
  .texture { position: absolute; inset: 0; }
  .back-carbon .brand-mark { left: 242px; top: 100px; width: 42px; height: 42px; }
  .back-carbon .brand-name { left: 0; width: 100%; text-align: center; top: 158px; font-size: 22px; }

  .back-dots .dots {
    position: absolute;
    background: radial-gradient(ellipse at center, var(--dot-tone), transparent 70%);
  }
  .back-dots .dots-top { left: -20px; top: -30px; width: 300px; height: 140px; }
  .back-dots .dots-bottom { left: 270px; top: 190px; width: 290px; height: 140px; }
  .back-dots .brand-mark { left: 236px; top: 92px; width: 54px; height: 54px; }
  .back-dots .brand-name { left: 0; width: 100%; text-align: center; top: 172px; font-size: 25px; }
</style>
</head>
<body>

<div class="view-label" style="left:157px; top:22px;">front</div>
<div class="view-label" style="left:735px; top:22px;">front-1</div>
<div class="view-label" style="left:165px; top:406px;">back</div>
<div class="view-label" style="left:730px; top:406px;">Back - 1</div>

<svg width="0" height="0" style="position:absolute">
  <defs>
    <symbol id="icon-phone" viewBox="0 0 24 24"><path d="M6.6 10.8a15 15 0 0 0 6.6 6.6l2.2-2.2c.3-.3.7-.4 1-.2 1.1.4 2.3.6 3.6.6.6 0 1 .4 1 1V20c0 .6-.4 1-1 1A17 17 0 0 1 3 4c0-.6.4-1 1-1h3.5c.6 0 1 .4 1 1 0 1.3.2 2.5.6 3.6.1.3 0 .7-.2 1z"/></symbol>
    <symbol id="icon-fax" viewBox="0 0 24 24"><path d="M6 3h10v5H6zM3 9h18v9h-3v3H6v-3H3zm5 7v3h8v-3z"/></symbol>
    <symbol id="icon-mobile" viewBox="0 0 24 24"><path d="M7 1h10c1 0 2 1 2 2v18c0 1-1 2-2 2H7c-1 0-2-1-2-2V3c0-1 1-2 2-2zm0 3v14h10V4z"/></symbol>
    <symbol id="icon-mail" viewBox="0 0 24 24"><path d="M2 5h20v14H2zm2 2v.5l8 5 8-5V7l-8 5z"/></symbol>
  </defs>
</svg>

<section class="card front" style="left:50px; top:62px;">
  <div class="brand-mark"></div>
  <div class="brand-name">Vantorin Kitchens</div>
  <div class="name-band">
    <div class="person-name">Marek Dolan</div>
    <div class="person-role">President</div>
  </div>
  <ul class="contact-list">
    <li><svg><use href="#icon-phone"/></svg>555.201.0147</li>
    <li><svg><use href="#icon-fax"/></svg>555.201.0183</li>
    <li><svg><use href="#icon-mobile"/></svg>555.318.2046</li>
    <li><svg><use href="#icon-mail"/></svg>marek@vantorinkitchens.ca</li>
  </ul>
  <div class="address">1820 - 47 St.<br>Northgate, AB T0X 1K2</div>
</section>

<section class="card front" style="left:628px; top:62px;">
  <div class="brand-mark"></div>
  <div class="brand-name">Vantorin Kitchens</div>
  <div class="name-band">
    <div class="person-name">Stefan Dolan</div>
    <div class="person-role">Director</div>
  </div>
  <ul class="contact-list">
    <li><svg><use href="#icon-phone"/></svg>555.201.0147</li>
    <li><svg><use href="#icon-fax"/></svg>555.201.0183</li>
    <li><svg><use href="#icon-mobile"/></svg>555.642.9051</li>
    <li><svg><use href="#icon-mail"/></svg>stefan@vantorinkitchens.ca</li>
  </ul>
  <div class="address">1820 - 47 St.<br>Northgate, AB T0X 1K2</div>
</section>

<section class="card back-carbon" style="left:56px; top:446px;">
  <div class="texture" role="img" aria-label="Fine dark carbon-fibre weave texture across the card"></div>
  <div class="brand-mark"></div>
  <div class="brand-name">Vantorin Kitchens</div>
</section>

<section class="card back-dots" style="left:624px; top:446px;">
  <div class="dots dots-top" role="img" aria-label="Perforated metal dot pattern fading in from the top left corner"></div>
  <div class="dots dots-bottom" role="img" aria-label="Perforated metal dot pattern fading in from the bottom right corner"></div>
  <div class="brand-mark"></div>
  <div class="brand-name">Vantorin Kitchens</div>
</section>

</body>
</html>
```